Tessmar Fahrwerkstatt
Sehr angenehme zusammenarbeit nicht aufdringlich und genau auf die Wünsche eingegangen. Wir werde sicher noch mehr zusammen Arbeiten. Gruss Lukas Hegemann Inhaber Tessmar Fahrwerkstatt
Zielgruppe
Dinks und Kunden mit viel Erfolg und hohem Ausgabepotential.
Aufgabenstellung
Unsere Firma vertreibt Fahrzeuge im Luxusbereich hauptgebiet Valmerra aber auch andere Sportwagen. Was uns fehlt ist ein optischer Wiedererkennugswert. Deshalb hätten wir gerne ein Visitenkarten Design und Briefpapier Design. Später soll auch noch eine Webseite mit gleichem Wiedererkennungswert entstehen. " Roter Faden "

```html
<!DOCTYPE html>
<html lang="de">
<head>
<meta charset="utf-8">
<title>Tessmar Fahrwerkstatt – Visitenkarte</title>
<link rel="stylesheet" href="https://fonts.googleapis.com/css2?family=Inconsolata:wght@500&display=swap">
<style>
  :root {
    --page-bg: #e4e4e2;
    --card-black: #050505;
    --card-edge: #1a1a1a;
    --brand-red: #8a1a1c;
    --deep-red: #3a0c0d;
    --text-white: #f2f2f2;
  }
  html, body {
    margin: 0;
    padding: 0;
    width: 1200px;
    height: 910px;
    overflow: hidden;
    background: var(--page-bg);
  }
  .canvas {
    position: relative;
    width: 1200px;
    height: 910px;
    display: flex;
    align-items: center;
    justify-content: center;
  }
  .business-card {
    position: relative;
    width: 470px;
    height: 710px;
    background: var(--card-black);
    overflow: hidden;
    box-shadow: 0 0 0 1px var(--card-edge);
  }
  .brand-dot {
    position: absolute;
    top: 92px;
    left: 50%;
    width: 54px;
    height: 54px;
    margin-left: -27px;
    border-radius: 50%;
    background: var(--brand-red);
  }
  .wordmark {
    position: absolute;
    top: 200px;
    left: 0;
    right: 0;
    margin: 0;
    text-align: center;
    font-family: "Inconsolata", monospace;
    font-weight: 500;
    font-size: 34px;
    line-height: 1.2;
    letter-spacing: 0.12em;
    font-variant: small-caps;
    color: var(--text-white);
  }
  .wordmark span { display: block; }
  .backdrop-visual {
    position: absolute;
    left: 0;
    right: 0;
    bottom: 0;
    height: 400px;
    background:
      radial-gradient(ellipse 60% 55% at 68% 45%, #1c1c1c 0%, rgba(12,12,12,0) 70%),
      radial-gradient(ellipse 75% 50% at 35% 75%, var(--deep-red) 0%, rgba(58,12,13,0) 72%),
      var(--card-black);
  }
</style>
</head>
<body>
  <main class="canvas">
    <article class="business-card">
      <div class="brand-dot"></div>
      <h1 class="wordmark"><span>Tessmar</span><span>Fahrwerkstatt</span></h1>
      <div class="backdrop-visual" role="img" aria-label="Dunkle Hintergrundaufnahme eines Sportwagen-Details mit rotem Schimmer"></div>
    </article>
  </main>
</body>
</html>
```